Business card for a new cabinet shop company named Veloran Cabinets for high end cabinets

Design a business card, thinking dark rich green with colours to speak of high end luxury ie; cream, gold, black possibly

Mitchell Tarrowby
Director Craftsman
Email: info@veloranjoinery-example.com.au
Instagram : @veloran.cabinets

```html
<!DOCTYPE html>
<html lang="en">
<head>
<meta charset="utf-8">
<title>Veloran Cabinets — Business Card</title>
<link rel="stylesheet" href="https://fonts.googleapis.com/css2?family=Montserrat:wght@400;700&family=Poppins:wght@400;500&display=swap">
<style>
  :root {
    --backdrop: #979797;
    --card: #ffffff;
    --gold: #c9a862;
    --ink: #111111;
  }
  * { margin: 0; padding: 0; box-sizing: border-box; }
  html, body {
    width: 1200px;
    height: 1108px;
    overflow: hidden;
    background: var(--backdrop);
  }
  .canvas {
    position: relative;
    width: 1200px;
    height: 1108px;
  }
  .card {
    position: absolute;
    left: 242px;
    width: 715px;
    height: 409px;
    background: var(--card);
    border-radius: 30px;
  }
  .card--front { top: 119px; }
  .card--back { top: 580px; }

  /* Front */
  .brand {
    position: absolute;
    left: 64px;
    top: 125px;
    display: flex;
    align-items: center;
    gap: 22px;
  }
  .brand__mark {
    width: 58px;
    height: 58px;
    background: var(--gold);
  }
  .brand__name {
    font-family: "Poppins", sans-serif;
    font-weight: 500;
    font-size: 50px;
    letter-spacing: 1px;
    color: var(--gold);
    line-height: 1;
  }

  /* Back */
  .identity {
    position: absolute;
    right: 409px;
    top: 171px;
    text-align: right;
    font-family: "Montserrat", sans-serif;
  }
  .identity__name {
    font-weight: 700;
    font-size: 26px;
    color: var(--gold);
    line-height: 1.15;
  }
  .identity__role {
    font-weight: 400;
    font-size: 17px;
    color: var(--ink);
    margin-top: 6px;
  }
  .divider {
    position: absolute;
    left: 325px;
    top: 178px;
    width: 2px;
    height: 53px;
    background: var(--gold);
  }
  .contact {
    position: absolute;
    left: 348px;
    top: 178px;
    list-style: none;
    font-family: "Montserrat", sans-serif;
    font-size: 16.5px;
    color: var(--ink);
  }
  .contact__item {
    display: flex;
    align-items: center;
    gap: 10px;
    height: 26px;
    margin-bottom: 2px;
  }
  .contact__icon {
    width: 14px;
    height: 14px;
    flex: none;
  }
  .contact__dot {
    width: 13px;
    height: 13px;
    border-radius: 50%;
    background: var(--gold);
    flex: none;
    margin: 0 1px 0 0;
  }
</style>
</head>
<body>
  <main class="canvas">
    <section class="card card--front" aria-label="Card front">
      <div class="brand">
        <span class="brand__mark" aria-hidden="true"></span>
        <span class="brand__name">Veloran Cabinets</span>
      </div>
    </section>

    <section class="card card--back" aria-label="Card back">
      <div class="identity">
        <p class="identity__name">Mitchell Tarrowby</p>
        <p class="identity__role">Director Craftsman</p>
      </div>
      <span class="divider" aria-hidden="true"></span>
      <ul class="contact">
        <li class="contact__item">
          <svg class="contact__icon" viewBox="0 0 14 14" aria-hidden="true">
            <rect x="0.5" y="3" width="13" height="9" fill="var(--gold)"/>
            <path d="M0.5 3 L7 8 L13.5 3" fill="none" stroke="#fff" stroke-width="1.2"/>
          </svg>
          <span>info@veloranjoinery-example.com.au</span>
        </li>
        <li class="contact__item">
          <span class="contact__dot" aria-hidden="true"></span>
          <span>@veloran.cabinets</span>
        </li>
      </ul>
    </section>
  </main>
</body>
</html>
```